IT Company requires new Business Card design.

Over the years we have had a few different business card designs. We are now due for new cards across the board for all staff. We felt this would be a good time to start fresh with a new design. Our traditional card simply had our details on the front, and a list of services on the back. We don't particularly need the list of services, we have had cards where the only thing on the rear of the card was our logo.
Feel free to be creative, we would like our tag line "Complete IT Management" to appear at some point, doesn't necessarily have to be with the logo.
I have attached samples and drafts of various previous cards we have used over the years.

```html
<!DOCTYPE html>
<html lang="en">
<head>
<meta charset="utf-8">
<title>Harbourcrest IT – Business Card Back</title>
<link rel="stylesheet" href="https://fonts.googleapis.com/css2?family=Open+Sans:ital,wght@0,300;0,600;1,400&display=swap">
<style>
  :root {
    --card-bg: #1f1f1f;
    --card-bg-deep: #191919;
    --heading: #f2f2f2;
    --service-text: #dcdcdc;
    --web-text: #f0f0f0;
  }
  * { margin: 0; padding: 0; box-sizing: border-box; }
  html, body {
    width: 1200px;
    height: 669px;
    overflow: hidden;
    background: var(--card-bg-deep);
  }
  .card {
    position: relative;
    width: 1200px;
    height: 669px;
    overflow: hidden;
    font-family: "Open Sans", sans-serif;
  }
  .card-texture {
    position: absolute;
    inset: 0;
    background: radial-gradient(ellipse at 40% 40%, var(--card-bg) 0%, var(--card-bg-deep) 100%);
  }
  .tagline {
    position: absolute;
    left: 41px;
    top: 117px;
    font-size: 34px;
    font-weight: 600;
    line-height: 1;
    letter-spacing: 0.3px;
    color: var(--heading);
  }
  .service-list {
    position: absolute;
    top: 330px;
    list-style: none;
    font-size: 27px;
    font-weight: 300;
    line-height: 37.6px;
    color: var(--service-text);
    white-space: nowrap;
  }
  .service-list--hardware { left: 40px; }
  .service-list--infrastructure { left: 366px; }
  .service-list--online { left: 805px; top: 327px; }
  .web-address {
    position: absolute;
    right: 40px;
    top: 613px;
    font-size: 27px;
    font-style: italic;
    font-weight: 400;
    line-height: 1;
    color: var(--web-text);
  }
</style>
</head>
<body>
<main class="card">
  <div class="card-texture" role="img" aria-label="Dark charcoal carbon-fibre weave texture"></div>

  <h1 class="tagline">Complete IT Management</h1>

  <ul class="service-list service-list--hardware">
    <li>Networking</li>
    <li>Servers</li>
    <li>Workstations</li>
    <li>Laptops</li>
    <li>Firewalls</li>
  </ul>

  <ul class="service-list service-list--infrastructure">
    <li>Data Cabling</li>
    <li>All electrical Work</li>
    <li>Server Racks</li>
    <li>Network Infrastructure</li>
    <li>Off site back up</li>
  </ul>

  <ul class="service-list service-list--online">
    <li>ADSL Connections</li>
    <li>Web Hosting</li>
    <li>Web Design</li>
    <li>Website Maintenance</li>
    <li>Domain Names PABX systems</li>
  </ul>

  <p class="web-address">www.harbourcrestit.com.au</p>
</main>
</body>
</html>
```